wedding invitation card

Requirement:
1. White background, pink elements on the card, simple elegant looking
2. content:
Please join us as we celebrate new beginnings, new dreams,
and most importantly, new love at the marriage of
Miss Lei Hsu and Mr. Mingtao Pan
Friday, The First of January
Two Thousand Fifteen at Eleven o’clock
Coral Mist Hotel Palm Garden Deck.

Reception will be followed at Lantern Hall at Half-Past Twelve o'clock

Please RSVP before December 18th 2015 by email: hsulei0817@mailbrook.example

3. Flat paper
4. be able to change the size of the design according to printing requirement

Industry/Entity Type

Wedding

```html
<!DOCTYPE html>
<html lang="en">
<head>
<meta charset="utf-8">
<title>Wedding Invitation – Lei Hsu &amp; Mingtao Pan</title>
<link rel="stylesheet" href="https://fonts.googleapis.com/css2?family=Parisienne&family=Cormorant+Garamond:ital,wght@1,400;1,600;1,700&family=Cinzel:wght@600&display=swap">
<style>
  :root {
    --backdrop: #d9d9d9;
    --paper: #ffffff;
    --edge: #9a9a9a;
    --ink: #111111;
    --muted: #7d7d7d;
    --soft-grey: #c4c4c4;
    --pink: #d6297f;
    --pink-light: #f2b6cf;
    --rose: #e55aa0;
    --violet: #9a4fa8;
  }
  html, body {
    margin: 0;
    padding: 0;
    overflow: hidden;
  }
  body {
    width: 1200px;
    height: 766px;
    background: var(--backdrop);
    position: relative;
  }
  .card {
    position: absolute;
    background: var(--paper);
    border: 1px solid var(--edge);
    box-sizing: border-box;
  }
  .card--front { left: 73px; top: 122px; width: 524px; height: 263px; }
  .card--back  { left: 79px; top: 431px; width: 524px; height: 262px; }
  .card--open  { left: 638px; top: 91px; width: 524px; height: 525px; }

  .bouquet {
    position: absolute;
    left: 220px; top: 73px;
    width: 80px; height: 72px;
    border-radius: 50% 50% 45% 45%;
    background: radial-gradient(circle at 45% 40%, var(--rose), var(--violet));
  }
  .front-title {
    position: absolute;
    left: 0; right: 0; top: 140px;
    margin: 0;
    text-align: center;
    font-family: "Parisienne", cursive;
    font-weight: 400;
    font-size: 46px;
    color: var(--soft-grey);
  }

  .rosebud {
    position: absolute;
    left: 266px; top: 120px;
    width: 22px; height: 22px;
    border-radius: 50%;
    background: radial-gradient(circle at 40% 40%, var(--rose), var(--violet));
  }
  .back-date {
    position: absolute;
    left: 0; width: 520px; top: 143px;
    margin: 0;
    text-align: center;
    font-family: "Cormorant Garamond", serif;
    font-style: italic;
    font-size: 11px;
    color: var(--muted);
  }

  .fold {
    position: absolute;
    left: 0; right: 0; top: 270px;
    height: 0;
    border-top: 1px solid #ececec;
  }
  .invite-body {
    position: absolute;
    left: 0; right: 0; top: 330px;
    text-align: center;
  }
  .intro {
    margin: 0;
    font-family: "Cormorant Garamond", serif;
    font-style: italic;
    font-weight: 700;
    font-size: 12.5px;
    line-height: 16px;
    color: var(--ink);
  }
  .couple {
    margin: 8px 0 0;
    font-family: "Parisienne", cursive;
    font-weight: 400;
    font-size: 30px;
    line-height: 36px;
    color: var(--ink);
  }
  .date-line {
    margin: 0;
    font-family: "Cinzel", serif;
    font-weight: 600;
    font-size: 7.5px;
    letter-spacing: 3px;
    text-transform: uppercase;
    color: var(--pink);
  }
  .details {
    margin: 6px 0 0;
    font-family: "Cormorant Garamond", serif;
    font-style: italic;
    font-size: 9px;
    line-height: 12px;
    color: var(--muted);
  }
  .details strong { font-weight: 700; }
  .divider {
    display: block;
    margin: 3px auto 2px;
  }
  .rsvp {
    margin: 0;
    font-family: "Cormorant Garamond", serif;
    font-style: italic;
    font-size: 9px;
    color: var(--muted);
  }
</style>
</head>
<body>

  <section class="card card--front">
    <div class="bouquet" role="img" aria-label="Watercolour bouquet of pink and violet roses tied with a purple ribbon"></div>
    <h1 class="front-title">Invitation</h1>
  </section>

  <section class="card card--back">
    <div class="rosebud" role="img" aria-label="Single small pink rose on a stem"></div>
    <p class="back-date">1.01.2016</p>
  </section>

  <section class="card card--open">
    <div class="fold"></div>
    <div class="invite-body">
      <p class="intro">Please join us as we celebrate new beginnings, new dreams,<br>and most importantly, new love at the marriage of</p>
      <p class="couple">Miss Lei Hsu &nbsp;and &nbsp;Mr. Mingtao Pan</p>
      <p class="date-line">Friday, the first of January</p>
      <p class="details">
        Two Thousand Fifteen at Eleven o’clock<br>
        <strong>Coral Mist Hotel</strong> Palm Garden Deck.<br>
        Reception will be followed at Lantern Hall at Half-Past Twelve o’clock
      </p>
      <svg class="divider" width="336" height="8" viewBox="0 0 336 8" aria-hidden="true">
        <line x1="0" y1="4" x2="163" y2="4" stroke="var(--pink-light)" stroke-width="1"/>
        <circle cx="168" cy="4" r="2" fill="var(--pink)"/>
        <line x1="173" y1="4" x2="336" y2="4" stroke="var(--pink-light)" stroke-width="1"/>
      </svg>
      <p class="rsvp">Please RSVP before December 18th 2015 by email: hsulei0817@mailbrook.example</p>
    </div>
  </section>

</body>
</html>
```